Redesign of business card for Cedar Ridge Mechanical

We are looking for a new design for our business cards for Cedar Ridge Mechanical. We are a plumbing & HVAC construction company, operating on the West Coast of Canada and USA. Logo attached.
Industry/Entity Type
Construction - Plumbing & HVAC
Contact Information for Business Card
Name, address, phone numbers, email, website address
Look and feel
Each slider illustrates characteristics of the customer's brand and the style your logo design should communicate.

```html
<!DOCTYPE html>
<html lang="en">
<head>
<meta charset="utf-8">
<title>Cedar Ridge Mechanical – Business Card</title>
<link href="https://fonts.googleapis.com/css2?family=Poppins:wght@300;400;600;700&display=swap" rel="stylesheet">
<style>
  :root {
    --stage: #232323;
    --ink: #111112;
    --card-dark: #1a1a1c;
    --paper: #ffffff;
    --rule: #2a2a2a;
  }
  * { box-sizing: border-box; margin: 0; padding: 0; }
  html, body { width: 1200px; height: 780px; overflow: hidden; }
  body {
    background: var(--stage);
    font-family: "Poppins", sans-serif;
    position: relative;
  }
  .card {
    position: absolute;
    top: 241px;
    width: 520px;
    height: 297px;
    border-radius: 6px;
    overflow: hidden;
    box-shadow: 0 18px 40px rgba(0,0,0,.45);
  }
  .card-front { left: 50px; background: var(--paper); color: var(--ink); }
  .card-back { left: 630px; background: var(--card-dark); border: 1px solid #2e2e30; }

  .front-band { position: absolute; inset: 0; }

  .wordmark {
    position: absolute;
    display: flex;
    align-items: center;
    gap: 10px;
    font-weight: 600;
    white-space: nowrap;
  }
  .wordmark-square {
    display: block;
    border: 3px solid currentColor;
    border-radius: 4px;
  }
  .card-front .wordmark { left: 250px; top: 36px; font-size: 17px; color: var(--ink); }
  .card-front .wordmark-square { width: 26px; height: 26px; }

  .person { position: absolute; left: 34px; top: 34px; text-align: right; }
  .person-name { font-size: 27px; line-height: 1.1; white-space: nowrap; }
  .person-name .first { font-weight: 700; }
  .person-name .last { font-weight: 300; }
  .person-title { font-size: 13px; font-weight: 400; margin-top: 2px; }

  .divider {
    position: absolute;
    left: 230px;
    top: 120px;
    width: 1px;
    height: 76px;
    background: var(--rule);
  }

  .contact-list {
    position: absolute;
    left: 250px;
    top: 118px;
    list-style: none;
    font-size: 15px;
    font-weight: 400;
    line-height: 26px;
  }
  .contact-list li { display: flex; align-items: center; gap: 9px; }
  .contact-list svg { width: 14px; height: 14px; flex: none; }

  .address {
    position: absolute;
    left: 30px;
    bottom: 12px;
    font-size: 12px;
    font-weight: 300;
    color: var(--paper);
    letter-spacing: .2px;
  }

  .card-back .wordmark {
    left: 50%;
    top: 50%;
    transform: translate(-50%, -50%);
    font-size: 24px;
    color: var(--paper);
    gap: 14px;
  }
  .card-back .wordmark-square { width: 36px; height: 36px; }
</style>
</head>
<body>

<section class="card card-front" aria-label="Business card front">
  <svg class="front-band" viewBox="0 0 520 297" preserveAspectRatio="none" aria-hidden="true">
    <path d="M0 52 C 40 190 240 262 520 258 L520 297 L0 297 Z" fill="var(--card-dark)"/>
    <path d="M14 70 C 60 196 250 256 500 252" fill="none" stroke="var(--paper)" stroke-width="3" stroke-linecap="round"/>
  </svg>

  <div class="person">
    <p class="person-name"><span class="first">Marta</span> <span class="last">Koval</span></p>
    <p class="person-title">Founder &amp; CEO</p>
  </div>

  <div class="wordmark"><span class="wordmark-square"></span>Cedar Ridge Mechanical</div>

  <span class="divider"></span>

  <ul class="contact-list">
    <li>
      <svg viewBox="0 0 24 24" aria-hidden="true"><path fill="currentColor" d="M6.6 10.8a15 15 0 0 0 6.6 6.6l2.2-2.2c.3-.3.7-.4 1-.2 1.1.4 2.3.6 3.6.6.6 0 1 .4 1 1V20c0 .6-.4 1-1 1A17 17 0 0 1 3 4c0-.6.4-1 1-1h3.5c.6 0 1 .4 1 1 0 1.3.2 2.5.6 3.6.1.3 0 .7-.2 1z"/></svg>
      (555) 214-3086
    </li>
    <li>
      <svg viewBox="0 0 24 24" aria-hidden="true"><path fill="currentColor" d="M3 5h18a1 1 0 0 1 1 1v12a1 1 0 0 1-1 1H3a1 1 0 0 1-1-1V6a1 1 0 0 1 1-1zm9 7 8-5H4z"/></svg>
      info@cedarridgemech.com
    </li>
    <li>
      <svg viewBox="0 0 24 24" aria-hidden="true"><circle cx="12" cy="12" r="9" fill="none" stroke="currentColor" stroke-width="2"/><path d="M3 12h18M12 3c3 3 3 15 0 18M12 3c-3 3-3 15 0 18" fill="none" stroke="currentColor" stroke-width="1.6"/></svg>
      www.cedarridgemech.com
    </li>
  </ul>

  <p class="address">1840 Harbor Ln. Suite 300 Portland, OR 97205</p>
</section>

<section class="card card-back" aria-label="Business card back">
  <div class="wordmark"><span class="wordmark-square"></span>Cedar Ridge Mechanical</div>
</section>

</body>
</html>
```